Lawn care business card

I am looking for a quality designed personal business card to represent the quality and elegant nature of our company. We separate ourselves in our market by the aesthetic value of our work, so I am looking for marketing material that does the same. We target our marketing high end customers, and we try to avoid price shoppers. I am open to all design options, so long as they are in line with our companies values.

We are tend to go with a retro look on everything from our logo and print material, to our uniforms. We like to portray and "old fashion" set of core values, with a modern elegance. So a wild and crazy look is out of the question.

Things I'd like on the card:
1.) Logo
2.) Phone number: (816) 555-2931
3.) Website: Verdelynkc.com
4.) Email: robertfairley@verdelynkc.com
5.) My name: Robert Fairley
6.) Facebook link: facebook.com/VerdelynGardenandGrounds
7.) Instagram: http://instagram.com/verdelynkc

Attached is a copy of our logo.

Reason: More time is needed to gather conclusive feedback from the members of our marketing team.

```html
<!DOCTYPE html>
<html lang="en">
<head>
<meta charset="utf-8">
<title>Verdelyn Garden &amp; Grounds — Business Card</title>
<link rel="stylesheet" href="https://fonts.googleapis.com/css2?family=Lato:wght@300;400&family=Questrial&display=swap">
<style>
  :root {
    --page-bg: #e9e7e3;
    --card-bg: #fbfbfa;
    --card-edge: #e2e2e0;
    --ink-dark: #3a3a3a;
    --ink-mid: #5c5c5c;
    --ink-light: #8a8a8a;
    --accent: #f07a1f;
    --row-line: #ececea;
  }
  * { margin: 0; padding: 0; box-sizing: border-box; }
  html, body {
    width: 1200px;
    height: 1023px;
    overflow: hidden;
    background: var(--page-bg);
  }
  .canvas {
    position: relative;
    width: 1200px;
    height: 1023px;
  }
  .card {
    position: absolute;
    left: 350px;
    top: 74px;
    width: 500px;
    height: 875px;
    background: linear-gradient(180deg, #ffffff 0%, var(--card-bg) 60%, #f4f4f2 100%);
    border: 1px solid var(--card-edge);
    box-shadow: 0 10px 30px rgba(0,0,0,0.12);
    font-family: "Questrial", "Century Gothic", sans-serif;
  }
  .card__name {
    position: absolute;
    top: 64px;
    right: 48px;
    font-family: "Lato", sans-serif;
    font-size: 34px;
    color: var(--ink-light);
    letter-spacing: 0.5px;
  }
  .card__name-first { font-weight: 300; }
  .card__name-last { font-weight: 400; color: var(--ink-mid); }

  .brand {
    position: absolute;
    top: 230px;
    left: 0;
    width: 100%;
    display: flex;
    align-items: center;
    justify-content: center;
    gap: 18px;
  }
  .brand__dot {
    width: 46px;
    height: 46px;
    border-radius: 50%;
    background: var(--accent);
  }
  .brand__name {
    font-family: "Questrial", sans-serif;
    font-size: 64px;
    color: var(--ink-dark);
    letter-spacing: 2px;
    text-transform: uppercase;
  }

  .contacts {
    position: absolute;
    top: 470px;
    left: 0;
    width: 100%;
    list-style: none;
  }
  .contact {
    display: flex;
    align-items: center;
    height: 72px;
    padding-left: 52px;
    border-top: 1px solid var(--row-line);
  }
  .contact:last-child { border-bottom: 1px solid var(--row-line); }
  .contact__icon {
    width: 34px;
    height: 34px;
    margin-right: 26px;
    flex-shrink: 0;
    fill: var(--accent);
  }
  .contact__text {
    font-size: 22px;
    color: var(--ink-mid);
    letter-spacing: 0.6px;
    white-space: nowrap;
  }
</style>
</head>
<body>
<main class="canvas">
  <article class="card">
    <p class="card__name"><span class="card__name-first">Robert</span> <span class="card__name-last">Fairley</span></p>

    <div class="brand">
      <span class="brand__dot"></span>
      <span class="brand__name">Verdelyn</span>
    </div>

    <ul class="contacts">
      <li class="contact">
        <svg class="contact__icon" viewBox="0 0 34 34" aria-hidden="true">
          <path d="M9 3c1 0 2 1 3 3l2 4c.5 1 0 2-1 3l-2 1c1.5 3.5 4.5 6.5 8 8l1-2c1-1 2-1.5 3-1l4 2c2 1 3 2 3 3 0 3-3 6-6 6C13 30 4 21 4 9c0-3 3-6 5-6z"/>
        </svg>
        <span class="contact__text">(816) 555-2931</span>
      </li>
      <li class="contact">
        <svg class="contact__icon" viewBox="0 0 34 34" aria-hidden="true">
          <path d="M3 8h28v18H3z M4 9l13 10 13-10" fill="none" stroke="#f07a1f" stroke-width="2.4" stroke-linejoin="round"/>
        </svg>
        <span class="contact__text">robertfairley@verdelynkc.com</span>
      </li>
      <li class="contact">
        <svg class="contact__icon" viewBox="0 0 34 34" aria-hidden="true">
          <circle cx="17" cy="17" r="14" fill="none" stroke="#f07a1f" stroke-width="2.4"/>
          <ellipse cx="17" cy="17" rx="6" ry="14" fill="none" stroke="#f07a1f" stroke-width="2"/>
          <path d="M3 17h28" stroke="#f07a1f" stroke-width="2"/>
        </svg>
        <span class="contact__text">www.Verdelynkc.com</span>
      </li>
      <li class="contact">
        <svg class="contact__icon" viewBox="0 0 34 34" aria-hidden="true">
          <circle cx="17" cy="17" r="12"/>
        </svg>
        <span class="contact__text">/VerdelynGardenandGrounds</span>
      </li>
      <li class="contact">
        <svg class="contact__icon" viewBox="0 0 34 34" aria-hidden="true">
          <circle cx="17" cy="17" r="12"/>
        </svg>
        <span class="contact__text">@verdelynkc</span>
      </li>
    </ul>
  </article>
</main>
</body>
</html>
```